Luxury Business Card Design for High-End Window Treatments

Gilded Slatworks
Custom Plantation Shutters & Architectural Shading Systems

⸻

BACK

Daniel Trevick
Owner

Custom Interior & Exterior Window Treatments

919-555-0148
gildedslatworks.com

I have included a picture that I’m hoping we can use on the back, but I’m also wondering if you can get rid of the ladder? Should we get rid of shutters , shades and blinds underneath Gilded Slatworks?

Target Market(s)

High-end residential homeowners, custom home builders, architects, interior designers, and luxury renovation clients seeking premium plantation shutters and motorized architectural shading systems.

Industry/Entity Type

Custom Window treatments

Contact Information for Business Card

Front Gilded Slatworks Custom Plantation Shutters Motorized Architectural Shading Systems BACK Daniel Trevick Owner 919-555-0148 GildedSlatworks.com Custom Interior & Exterior Window Treatments By Appointment

Requirements
Nice to have
• Not 100% sure on nice to halves or the color but you can definitely check out my website to get a better understanding of what I’m trying to do

```html
<!DOCTYPE html>
<html lang="en">
<head>
<meta charset="UTF-8">
<title>Gilded Slatworks — Business Card</title>
<link href="https://fonts.googleapis.com/css2?family=Poppins:wght@400;500;600&display=swap" rel="stylesheet">
<style>
  :root {
    --stage: #2a2a2b;
    --card: #141414;
    --gold: #c9a646;
    --gold-light: #e6cf7a;
    --gold-deep: #a8862f;
    --ink-soft: #e8e8e8;
    --sky: #6fa3d8;
    --foliage: #7d8a5c;
    --facade: #3b3f47;
  }
  * { box-sizing: border-box; margin: 0; padding: 0; }
  html, body {
    width: 1200px; height: 875px; overflow: hidden;
    background: var(--stage);
    font-family: "Poppins", sans-serif;
  }
  .stage {
    width: 1200px; height: 875px;
    display: flex; align-items: center; justify-content: center; gap: 40px;
  }
  .card {
    position: relative;
    width: 540px; height: 309px;
    background: var(--card);
    border-radius: 16px;
    overflow: hidden;
    box-shadow: 0 18px 40px rgba(0,0,0,0.45);
  }
  /* Front */
  .card-front .gold-edge {
    position: absolute; left: 0; right: 0; bottom: 0; height: 6px;
    background: linear-gradient(90deg, var(--gold-deep), var(--gold-light), var(--gold));
  }
  .card-front .wordmark {
    position: absolute; inset: 0;
    display: flex; flex-direction: column; justify-content: center; align-items: center;
    color: var(--gold);
    font-weight: 500; font-size: 54px; line-height: 1.05;
    letter-spacing: 0.5px;
  }
  .card-front .wordmark span:last-child { margin-left: 90px; }
  /* Back */
  .card-back .artwork {
    position: absolute; inset: 0; width: 100%; height: 100%;
  }
  .card-back .wordmark {
    position: absolute; left: 44px; top: 118px;
    color: var(--gold);
    font-weight: 500; font-size: 34px; line-height: 1.05;
  }
  .card-back .wordmark span { display: block; }
  .card-back .wordmark span:last-child { margin-left: 40px; }
  .contact {
    position: absolute; left: 44px; bottom: 30px;
    color: var(--ink-soft);
  }
  .contact .person-name {
    color: var(--gold); font-weight: 600; font-size: 17px; line-height: 1.1;
  }
  .contact .person-role {
    font-size: 10px; margin-bottom: 8px; letter-spacing: 0.3px;
  }
  .contact .line {
    display: flex; align-items: center; gap: 8px;
    font-size: 11px; line-height: 1.6;
  }
  .contact svg { width: 11px; height: 11px; fill: var(--gold); }
</style>
</head>
<body>
<main class="stage">

  <section class="card card-front" aria-label="Card front">
    <div class="wordmark"><span>Gilded</span><span>Slatworks</span></div>
    <div class="gold-edge"></div>
  </section>

  <section class="card card-back" aria-label="Card back">
    <svg class="artwork" viewBox="0 0 540 309" preserveAspectRatio="none">
      <defs>
        <linearGradient id="photoTone" x1="0" y1="0" x2="1" y2="1">
          <stop offset="0" stop-color="var(--sky)"/>
          <stop offset="0.45" stop-color="var(--foliage)"/>
          <stop offset="1" stop-color="var(--facade)"/>
        </linearGradient>
        <linearGradient id="swoosh" x1="0" y1="0" x2="1" y2="0">
          <stop offset="0" stop-color="var(--gold-deep)"/>
          <stop offset="0.6" stop-color="var(--gold-light)"/>
          <stop offset="1" stop-color="var(--gold)"/>
        </linearGradient>
      </defs>
      <path role="img" aria-label="Photo of a home porch fitted with exterior shading screens, pine trees and blue sky"
            fill="url(#photoTone)"
            d="M270,0 H540 V196 C430,222 310,178 262,108 C246,80 246,34 270,0 Z"/>
      <path fill="url(#swoosh)"
            d="M256,112 C308,188 432,228 540,204 V218 C428,244 300,200 256,112 Z"/>
    </svg>

    <div class="wordmark"><span>Gilded</span><span>Slatworks</span></div>

    <div class="contact">
      <div class="person-name">Daniel Trevick</div>
      <div class="person-role">Owner</div>
      <div class="line">
        <svg viewBox="0 0 24 24" aria-hidden="true"><path d="M6.6 10.8a15.1 15.1 0 0 0 6.6 6.6l2.2-2.2a1 1 0 0 1 1-.25 11.4 11.4 0 0 0 3.6.57 1 1 0 0 1 1 1V20a1 1 0 0 1-1 1A17 17 0 0 1 3 4a1 1 0 0 1 1-1h3.5a1 1 0 0 1 1 1c0 1.25.2 2.45.57 3.57a1 1 0 0 1-.25 1z"/></svg>
        <span>919-555-0148</span>
      </div>
      <div class="line">
        <svg viewBox="0 0 24 24" aria-hidden="true"><path d="M12 2a10 10 0 1 0 0 20 10 10 0 0 0 0-20zm6.9 6h-2.9a15.7 15.7 0 0 0-1.4-3.6A8 8 0 0 1 18.9 8zM12 4c.8 1.2 1.5 2.5 1.9 4h-3.8c.4-1.5 1.1-2.8 1.9-4zM4.3 14a8 8 0 0 1 0-4h3.4a16 16 0 0 0 0 4zm.8 2h2.9c.3 1.3.8 2.5 1.4 3.6A8 8 0 0 1 5.1 16zM8 8H5.1a8 8 0 0 1 4.3-3.6C8.8 5.5 8.4 6.7 8 8zm4 12c-.8-1.2-1.5-2.5-1.9-4h3.8c-.4 1.5-1.1 2.8-1.9 4zm2.3-6H9.7a14.5 14.5 0 0 1 0-4h4.6a14.5 14.5 0 0 1 0 4zm.3 5.6c.6-1.1 1.1-2.3 1.4-3.6h2.9a8 8 0 0 1-4.3 3.6zM16.3 14a16 16 0 0 0 0-4h3.4a8 8 0 0 1 0 4z"/></svg>
        <span>gildedslatworks.com</span>
      </div>
    </div>
  </section>

</main>
</body>
</html>
```